Magazine Template for National Charity

We need a magazine design for an Australian youth charity called Rhythm Crews Lifting FUtures (RCLF). We engage young people through street culture music, dance and mentoring programs, and help them to turn their lives around. Our charity's vision is to see every young person have someone who believes in them and the opportunity to live their potential.

The design should have places for images of our young people during programs(we've only provided a few for you), room for quotes from young people and supporters etc, and each double spread could be a snapshot of a different program.

We will need a design template that will allow us to add all the contents for the magazine, including a contents page, report from our Chairman (1 page), letter from CEO (1 page), and following achievements of our programs including 1. RCLF Camps (2 x double spread, total 4 pages), 2. Groove Labs (2 x double spread, total 4 pages) and 3. Mentoring (2 x double spread, total 4 pages). An audited financial report of 4 pages will be copied in after our program reports, and on the back of the magazine, we'll need space for all our supporter logos. I'd also like to include a short story or case-study about young people's transformation on each program page.

We need something that's got a bit of a street edge, to keep our youthful brand, but helps us to highlight our excellence as an innovative and cutting edge charity. The final design should be emotional, eye-catching, reflective of our creative spark, and inspiring. We currently have a brand that uses a fair bit of black & white with highlights of colour, however I dont want this to limit your creativity. We use a font called Octin Spraypaint Free for our logos and program names.

We would like to present our annual report as a magazine so that it is something that people will want to pick up and look at.

Target Market(s)

This is for general public and supporters, however we'd like to use our brand instead of a professional style for this report

Industry/Entity Type

Financial

Requirements
Must have
• See notes in task description - thank you!

We will give you a few images to use as a guide however we'd love to be able to play around with the images once we have a template (we'll add different ones and change pictures around to suit the program pages). We're providing these images so that you can get a feel for our culture and be inspired to put together the template, dont worry if you use the same photos more than once on the different pages to show as an example.
Nice to have
• We already have our charity logo, however we'd love to call this RCLF Mag, RCLF Magazine or Newest RCLF Rhythmania. We'd like it to replicate a real magazine, with colour and lots of interesting sections for information & stories, rather than a boring traditional annual report template.
Should not have
• We want this magazine to stand out, and we dont want a half-hearted charity design or a polished corporate style magazine.

We want to remain bold and contemporary, and on the commercial side with a street edge - have lots of fun & thank you so much - we're very excited!

```html
<!DOCTYPE html>
<html lang="en">
<head>
<meta charset="utf-8">
<title>RCLF Mag – The Groove Labs spread</title>
<link rel="stylesheet" href="https://fonts.googleapis.com/css2?family=Rubik+Dirt&family=Ubuntu:wght@400;700&display=swap">
<style>
  :root {
    --spread-blue: #241c8e;
    --paper-white: #ffffff;
    --photo-dark: #3a3a3a;
    --photo-light: #d9d9d9;
    --photo-warm: #c9a68a;
    --photo-teal: #4f8f88;
  }
  * { margin: 0; padding: 0; box-sizing: border-box; }
  html, body { width: 1200px; height: 855px; overflow: hidden; background: var(--spread-blue); }
  .spread {
    position: relative; width: 1200px; height: 855px;
    background: var(--spread-blue); color: var(--paper-white);
    font-family: "Ubuntu", Arial, sans-serif; overflow: hidden;
  }
  .display { font-family: "Rubik Dirt", "Impact", sans-serif; font-weight: 400; text-transform: uppercase; }

  .program-badge {
    position: absolute; left: 50px; top: 50px; width: 114px; height: 114px;
    border-radius: 50%; background: var(--paper-white); color: var(--spread-blue);
    display: flex; align-items: center; justify-content: center; text-align: center;
  }
  .program-badge span { display: block; transform: rotate(-14deg); font-size: 15px; line-height: 18px; }

  .headline {
    position: absolute; left: 46px; top: 172px;
    font-size: 56px; line-height: 82px; letter-spacing: 1px;
  }
  .pull-quote {
    position: absolute; right: 52px; top: 310px; text-align: right;
    font-size: 32px; line-height: 44px; letter-spacing: 1px;
  }

  .photo { position: absolute; border-radius: 50%; overflow: hidden; }
  .photo-girl-smiling {
    left: 48px; top: 350px; width: 304px; height: 304px;
    background: radial-gradient(circle at 40% 45%, var(--photo-light), #9a9a9a 55%, var(--photo-dark));
  }
  .photo-singer {
    left: 632px; top: 62px; width: 136px; height: 136px;
    background: radial-gradient(circle at 55% 40%, #e8d6c4, var(--photo-warm) 45%, #5a4f52);
  }
  .photo-performer {
    left: 923px; top: 475px; width: 250px; height: 250px;
    background: linear-gradient(135deg, #e6e1d6 0%, #cbb49e 40%, var(--photo-teal) 75%, #2f4a3c 100%);
  }

  .story { position: absolute; font-size: 10px; line-height: 14px; }
  .story h3 { font-size: 10px; font-weight: 700; line-height: 14px; }
  .story p { margin-bottom: 14px; }
  .story-left { left: 367px; top: 424px; width: 220px; }
  .story-top-right { left: 815px; top: 103px; width: 290px; }
  .story-bottom-right { left: 655px; top: 535px; width: 255px; text-align: right; }

  .brand-tab {
    position: absolute; right: 52px; top: 14px; height: 34px; padding: 3px 8px;
    background: var(--paper-white); color: var(--spread-blue); border-radius: 0 0 8px 8px;
    display: flex; align-items: center; gap: 6px;
  }
  .brand-tab .mark { width: 10px; height: 10px; background: var(--spread-blue); }
  .brand-tab .name { font-size: 11px; line-height: 12px; }

  .folio { position: absolute; bottom: 20px; display: flex; align-items: center; gap: 8px; font-size: 10px; }
  .folio .num {
    background: var(--paper-white); color: var(--spread-blue); font-weight: 700;
    font-size: 13px; padding: 2px 3px; line-height: 15px;
  }
  .folio-left { left: 45px; }
  .folio-right { right: 48px; }
</style>
</head>
<body>
<main class="spread">

  <div class="program-badge display"><span>The<br>Groove<br>Labs</span></div>

  <h1 class="headline display">“Ak dedef eaaf<br>pajed tofdu”</h1>

  <div class="photo photo-girl-smiling" role="img" aria-label="Black and white photo of a young participant smiling at a program session"></div>

  <article class="story story-left">
    <h3>HEADING</h3>
    <p>Every Tuesday night the hall fills with beats, rhymes and laughter as young people take the mic and find a voice they never knew they had.</p>
    <p>Mentors work side by side with each crew, building trust through music, dance and honest talk that keeps everyone coming back each week.</p>
    <p>For many it is the first time someone has listened without judging. Skills grow fast, but confidence grows faster. By the end of the term each crew writes, records and performs an original track for family, friends and the wider community at a packed showcase night that nobody forgets.</p>
    <p>Next year we plan to open two new labs in regional towns, giving even more young people the chance to create, connect and shine.</p>
  </article>

  <div class="photo photo-singer" role="img" aria-label="Photo of a young woman singing into a microphone on stage"></div>

  <article class="story story-top-right">
    <h3>HEADING</h3>
    <p>Jess joined the labs at fifteen, shy and unsure. Six months later she led the closing act in front of three hundred people.</p>
    <p>Her mentor helped her shape raw lyrics into songs that tell her story with strength and pride.</p>
    <p>Now she volunteers each week, helping new crew members take their first steps on stage and behind the desk.</p>
  </article>

  <blockquote class="pull-quote display">“Ak dedef eaaf pajed tofdu<br>dfjf jdfdshjf jadfkhjhfj<br>ajfhjdfkjhdlkh djfhdlhf”</blockquote>

  <article class="story story-bottom-right">
    <h3>HEADING</h3>
    <p>Dance crews meet twice a week to train, plan routines and share ideas, turning street moves into full stage shows.</p>
    <p>Coaches teach more than steps; they teach teamwork, focus and the belief that hard work pays off.</p>
    <p>Several dancers have since joined youth companies and now mentor younger crews of their own.</p>
  </article>

  <div class="photo photo-performer" role="img" aria-label="Photo of a performer in front of a colourful mural"></div>

  <div class="brand-tab">
    <span class="mark"></span>
    <span class="name display">Rhythm Crews<br>Lifting Futures</span>
  </div>

  <footer class="folio folio-left"><span class="num">10</span><span>the power of music</span></footer>
  <footer class="folio folio-right"><span>www.rclf.org.au</span><span class="num">11</span></footer>

</main>
</body>
</html>
```